Branding Guide and Website for Q7Systems

Need an experienced Graphics Designer with a proven track record to create a design and branding guide for all media formats. From this guide you will then create a new website design for Q7systems.com.
There will be 8 pages (to start) with the new website. Each page will have multiple features and panels each need to have individual attention and customization that collectively fit together into a single cohesive look and feel.
We have not been able to get good designs I’m attaching one version which is the best we’ve received which is not bad but needs to be polished up better and the images need to change. I’d like to have some other accent colors but not too much I like the white, dark blue, gray, dark gray style.
Here are some sites that I like –
http://www.brelvant.com/
https://www.vontaric.com/ (layout good, graphics not great)
http://www.glastrek.com/ (good layout and graphics, too much animation)
https://www.pendrowix.com/ (a little boring but the colors and some of the top images are good)
https://www.tarnowelk.com/ (a little over the top colors are off but they have some good info graphics)
We don’t expect you will code the site however if you have that capability we’ll need it responsive/flat for mobile. Otherwise we can find someone to do the programming and we’ll just need the design files and images.
Branding guide will be used for web, email, print etc. so you’ll need to consider all guidelines for all formats. That is about it let me know if any questions we can have a call to discuss further if it is easier.
Not sure why they want a minimum of 300 words I’m done now but apparently have to keep typing so that is what I’m doing and Ok I’m at 300 words, almost there and we’re here now.

Target Market(s)

Customers looking for IT Services, Private Cloud, Security Services, Advanced Support, Fully Managed or Co-Managed IT.

Industry/Entity Type

It Company

Number of Pages Required

5+ page

Font styles to use
Sans Serif

Colors
0255a3
959595
e6e6e6
ffffff

Requirements
Must have
• Clean, professional and modern look using iconography, info graphics, flat etc.

```html
<!DOCTYPE html>
<html lang="en">
<head>
<meta charset="utf-8">
<title>Q7 Systems — IT Service Excellence</title>
<link href="https://fonts.googleapis.com/css2?family=Open+Sans:wght@400;600;700;800&display=swap" rel="stylesheet">
<style>
:root{
  --blue:#0255a3;
  --blue-dark:#013a73;
  --gray:#959595;
  --gray-light:#e6e6e6;
  --white:#ffffff;
  --ink:#2b2b2b;
  --text:#6b6b6b;
  --footer:#232323;
  --footer-2:#1a1a1a;
  --accent:#f7931e;
}
*{box-sizing:border-box;margin:0;padding:0}
html,body{width:1200px;height:2704px;overflow:hidden}
body{font-family:"Open Sans",Arial,sans-serif;color:var(--text);background:var(--white);font-size:14px;line-height:1.6}
.page{position:relative;width:1200px;height:2704px}

/* header */
.site-header{height:100px;display:flex;align-items:center;justify-content:space-between;padding:0 44px}
.brand{display:flex;align-items:center;gap:10px;font-weight:700;font-size:24px;color:var(--blue)}
.brand-mark{width:20px;height:20px;background:var(--blue)}
.main-nav{display:flex;gap:4px}
.main-nav a{font-size:11px;font-weight:600;color:var(--ink);text-decoration:none;padding:10px 16px;letter-spacing:.4px}
.main-nav a.active{background:var(--blue);color:var(--white)}

/* hero */
.hero{position:relative;height:500px;background:linear-gradient(100deg,#0b2f63 0%,#0a4c97 55%,#1673c8 100%);color:var(--white);overflow:hidden}
.hero-copy{position:absolute;left:110px;top:160px}
.hero h1{font-size:42px;font-weight:800;letter-spacing:1px;line-height:1.1}
.hero p{font-size:15px;margin-top:10px;opacity:.9}
.btn-accent{display:inline-block;margin-top:34px;background:var(--accent);color:var(--white);font-size:12px;font-weight:700;padding:12px 22px;letter-spacing:.6px}
.hero-visual{position:absolute;left:560px;top:40px;width:460px;height:420px;border-radius:50%;background:radial-gradient(circle,rgba(120,190,255,.55) 0%,rgba(40,110,200,.25) 55%,rgba(10,60,130,0) 72%)}
.hero-arrow{position:absolute;top:226px;width:36px;height:48px;background:rgba(0,0,0,.25);display:flex;align-items:center;justify-content:center}
.hero-arrow.left{left:0}.hero-arrow.right{right:0}

/* sections */
.section-title{text-align:center;font-size:24px;font-weight:800;color:var(--ink);letter-spacing:.5px}
.section-title::after{content:"";display:block;width:50px;height:3px;background:var(--blue);margin:10px auto 0}
.section-intro{text-align:center;max-width:560px;margin:16px auto 0;font-size:13px}

.what-we-do{padding:58px 0 0;height:548px;border-bottom:1px solid var(--gray-light)}
.services{display:grid;grid-template-columns:repeat(3,300px);column-gap:60px;row-gap:46px;justify-content:center;margin-top:52px}
.service{display:flex;gap:16px}
.service svg{flex:none}
.service h3{font-size:17px;font-weight:600;color:var(--ink);line-height:1.3}
.service p{font-size:12px;margin-top:6px}

.help{padding:120px 0 0;height:572px}
.help-grid{display:grid;grid-template-columns:repeat(4,235px);gap:28px;justify-content:center;margin-top:40px}
.help-photo{height:156px}
.help-card h3{text-align:center;font-size:17px;font-weight:600;color:var(--ink);margin-top:16px}
.help-card p{text-align:center;font-size:12px;margin-top:4px;padding:0 12px}

.partners{height:180px;padding-top:4px}
.partners-note{text-align:center;font-size:12px}
.partner-row{display:flex;justify-content:center;gap:64px;margin-top:30px;align-items:center}
.partner{font-size:24px;font-weight:700;color:var(--gray)}

.testimonials{background:#f4f4f4;height:320px;padding-top:52px}
.quotes{display:grid;grid-template-columns:repeat(3,300px);gap:60px;justify-content:center;margin-top:46px}
.quote p{font-style:italic;text-align:center;font-size:13px}
.quote cite{display:block;text-align:center;font-style:normal;color:var(--blue);font-weight:600;font-size:13px;margin-top:12px}

.different{position:relative;height:348px;padding-top:60px}
.different p{text-align:center;max-width:680px;margin:24px auto 0;font-size:13px}
.btn-primary{display:block;width:180px;margin:40px auto 0;background:var(--blue);color:var(--white);text-align:center;font-size:12px;font-weight:700;padding:14px 0;letter-spacing:.6px}
.different-figure{position:absolute;right:0;top:10px;width:180px;height:330px;background:linear-gradient(180deg,#f0f0f0,#dfe6ee)}

/* footer */
.site-footer{height:316px;background:var(--footer);color:#bdbdbd;display:grid;grid-template-columns:330px 260px 290px 1fr;padding:40px 70px 0;font-size:12px;position:relative}
.social{display:flex;gap:8px}
.social span{width:28px;height:28px;border:2px solid #bdbdbd;border-radius:50%}
.legal{margin-top:20px;line-height:1.8}
.site-footer h4{color:var(--white);font-size:17px;font-weight:600;margin-bottom:16px}
.site-footer address{font-style:normal;line-height:1.9}
.field{width:220px;height:34px;background:var(--white);margin-bottom:10px;color:#999;padding:8px 10px;font-size:12px}
.btn-submit{display:inline-block;background:var(--blue);color:var(--white);font-weight:700;font-size:12px;padding:8px 18px}
.browse li{list-style:none;line-height:2}
.browse li::before{content:"›";color:var(--blue);margin-right:8px}
.footer-bar{position:absolute;left:0;right:0;bottom:0;height:34px;background:var(--footer-2)}
</style>
</head>
<body>
<div class="page">

<header class="site-header">
  <div class="brand"><span class="brand-mark"></span>Q7 Systems</div>
  <nav class="main-nav">
    <a class="active" href="#">HOME</a>
    <a href="#">MANAGED SERVICES</a>
    <a href="#">CORPORATE CLOUD</a>
    <a href="#">CLOUD SOLUTIONS</a>
    <a href="#">NETWORK OPERATIONS</a>
    <a href="#">SERVICES</a>
    <a href="#">COMPANY</a>
  </nav>
</header>

<section class="hero">
  <div class="hero-visual" role="img" aria-label="Illustration of a cloud connected to a ring of IT service icons"></div>
  <div class="hero-copy">
    <h1>IT SERVICE EXCELLENCE</h1>
    <p>Driving for Continuous Service Improvement for Our Clients</p>
    <span class="btn-accent">GET STARTED NOW</span>
  </div>
  <div class="hero-arrow left"><svg width="12" height="20"><path d="M10 2 2 10l8 8" fill="none" stroke="#fff" stroke-width="2"/></svg></div>
  <div class="hero-arrow right"><svg width="12" height="20"><path d="M2 2l8 8-8 8" fill="none" stroke="#fff" stroke-width="2"/></svg></div>
</section>

<section class="what-we-do">
  <h2 class="section-title">WHAT WE DO</h2>
  <p class="section-intro">Providing <b style="color:var(--blue)">World Class</b> IT services to businesses that need reliable, secure and modern systems to grow every day.</p>
  <div class="services">
    <div class="service">
      <svg width="40" height="40" viewBox="0 0 40 40" fill="none" stroke="#0255a3" stroke-width="2"><circle cx="20" cy="20" r="8"/><path d="M20 4v6M20 30v6M4 20h6M30 20h6M9 9l4 4M27 27l4 4M31 9l-4 4M9 31l4-4"/></svg>
      <div><h3>Managed Services</h3><p>We provide comprehensive technology management, IT services and support. Whether our engineers...</p></div>
    </div>
    <div class="service">
      <svg width="40" height="40" viewBox="0 0 40 40" fill="none" stroke="#0255a3" stroke-width="2"><path d="M11 30h20a7 7 0 0 0 0-14 10 10 0 0 0-19-2 8 8 0 0 0-1 16z"/></svg>
      <div><h3>Private Cloud</h3><p>We host systems and applications on our own cloud to improve speed, resilience and business value.</p></div>
    </div>
    <div class="service">
      <svg width="40" height="40" viewBox="0 0 40 40" fill="none" stroke="#0255a3" stroke-width="2"><rect x="10" y="18" width="20" height="16" rx="2"/><path d="M14 18v-5a6 6 0 0 1 12 0v5"/></svg>
      <div><h3>Security Services</h3><p>To prevent intrusion and maintain uptime in your system we protect data at every layer of defence.</p></div>
    </div>
    <div class="service">
      <svg width="40" height="40" viewBox="0 0 40 40" fill="none" stroke="#0255a3" stroke-width="2"><path d="M8 22v-3a12 12 0 0 1 24 0v3"/><rect x="6" y="22" width="6" height="10" rx="2"/><rect x="28" y="22" width="6" height="10" rx="2"/></svg>
      <div><h3>Advanced Support</h3><p>Skilled engineers respond fast to incidents, keep devices healthy and resolve issues before users notice them.</p></div>
    </div>
    <div class="service">
      <svg width="40" height="40" viewBox="0 0 40 40" fill="none" stroke="#0255a3" stroke-width="2"><rect x="15" y="5" width="10" height="8"/><rect x="4" y="27" width="10" height="8"/><rect x="26" y="27" width="10" height="8"/><path d="M20 13v7M9 27v-7h22v7"/></svg>
      <div><h3>Network Services</h3><p>Every organization needs a dependable network for company connectivity and reliable access to every critical system.</p></div>
    </div>
    <div class="service">
      <svg width="40" height="40" viewBox="0 0 40 40" fill="none" stroke="#0255a3" stroke-width="2"><path d="M32 20a12 12 0 1 1-4-9"/><path d="M29 5v7h-7"/></svg>
      <div><h3>Disaster Recovery</h3><p>Fully tested recovery plans keep your business running if systems fail, so downtime stays short and data stays safe.</p></div>
    </div>
  </div>
</section>

<section class="help">
  <h2 class="section-title">HOW CAN WE HELP YOUR BUSINESS?</h2>
  <p class="section-intro">Our customers leverage trusted experts to provide <b style="color:var(--blue)">complete end-to-end technology</b> management whether they need one service or a fully outsourced team.</p>
  <div class="help-grid">
    <div class="help-card">
      <div class="help-photo" role="img" aria-label="Photo of network cables plugged into a switch" style="background:linear-gradient(135deg,#2a3e5c,#7d8ea6)"></div>
      <h3>Your Network</h3><p>Consistent, reliable connectivity across offices and remote users.</p>
    </div>
    <div class="help-card">
      <div class="help-photo" role="img" aria-label="Photo of a digital padlock on a blue circuit screen" style="background:linear-gradient(135deg,#0b2a5a,#c0395a)"></div>
      <h3>Your Web Presence</h3><p>We protect and host your websites with constant monitoring.</p>
    </div>
    <div class="help-card">
      <div class="help-photo" role="img" aria-label="Photo of hands typing on a laptop" style="background:linear-gradient(135deg,#3b3b3b,#9c9c9c)"></div>
      <h3>Your Applications</h3><p>Business applications delivered securely in the cloud or on site.</p>
    </div>
    <div class="help-card">
      <div class="help-photo" role="img" aria-label="Photo of an engineer working in a server room" style="background:linear-gradient(135deg,#1e2d44,#8aa1bd)"></div>
      <h3>Your Piece of Mind</h3><p>Work with us for a structured IT strategy and proactive management.</p>
    </div>
  </div>
</section>

<section class="partners">
  <p class="partners-note">Trusted by growing teams across many industries to keep their systems secure and online. <b style="color:var(--blue)">See our clients</b></p>
  <div class="partner-row">
    <span class="partner">Corvane</span>
    <span class="partner">Meltrix</span>
    <span class="partner">Lumigraph</span>
    <span class="partner">Framestock</span>
    <span class="partner">Quadrant</span>
  </div>
</section>

<section class="testimonials">
  <h2 class="section-title">WHAT ARE PEOPLE SAYING ABOUT Q7 SYSTEMS</h2>
  <div class="quotes">
    <div class="quote"><p>“Since switching to Q7 Systems our network has been stable, our support tickets close quickly and our team can finally focus on the work that matters most to clients.”</p><cite>Dana Reyes, City Name</cite></div>
    <div class="quote"><p>“Their engineers planned our cloud move carefully, kept every office informed and finished ahead of schedule. We feel safer and spend far less time on everyday IT problems.”</p><cite>Dana Reyes, City Name</cite></div>
    <div class="quote"><p>“A responsive, honest partner. Monthly reports are clear, security reviews are thorough and the help desk always answers with real people who know our systems well.”</p><cite>Dana Reyes, City Name</cite></div>
  </div>
</section>

<section class="different">
  <h2 class="section-title">WE ARE DIFFERENT</h2>
  <p>We build long partnerships rather than quick fixes. Every client gets a dedicated team, a clear roadmap and honest advice about what their business really needs. Our engineers plan, secure and support your technology so it grows with you, with fair pricing and service levels you can count on every single day.</p>
  <span class="btn-primary">HOW IT WORKS</span>
  <div class="different-figure" role="img" aria-label="Illustrated character of a friendly IT consultant"></div>
</section>

<footer class="site-footer">
  <div>
    <div class="social"><span></span><span></span><span></span></div>
    <p class="legal">© 2016 Q7Systems<br>All Rights Reserved<br>Privacy Policy</p>
  </div>
  <div>
    <h4>Contact us</h4>
    <address>1450 Harbor Point Dr, Suite 210<br>Lakeview, CA 90210<br>1 (555) 014-7720<br>hello@q7systems.com</address>
  </div>
  <div>
    <h4>Newsletter</h4>
    <div class="field">Name</div>
    <div class="field">Email Address</div>
    <span class="btn-submit">SUBMIT</span>
  </div>
  <div>
    <h4>Browse</h4>
    <ul class="browse">
      <li>Managed Services</li>
      <li>Private Cloud</li>
      <li>Cloud Solutions</li>
      <li>Network Operations</li>
      <li>Services</li>
      <li>Company</li>
    </ul>
  </div>
  <div class="footer-bar"></div>
</footer>

</div>
</body>
</html>
```